Oral Surgeon Referral Pads

Hello. We need referral pads for Dr Elsabet Quorvane, DDS board certified oral surgeon's new office - Harrowgate Dunmere Oral & Maxillofacial Surgery. See logo uploaded. See some images we would like included
Updates

Designs look the same

Font styles to use
Serif
Script

Colors
00AB8E
00BBA5
67D7C9
C6EFE9
E9F9F6

Requirements
Must have
• Color Pantone 623c. Also foldable business cards

```html
<!DOCTYPE html>
<html lang="en">
<head>
<meta charset="utf-8">
<title>Harrowgate Dunmere Oral &amp; Maxillofacial Surgery – Business Card</title>
<link rel="stylesheet" href="https://fonts.googleapis.com/css2?family=Open+Sans:wght@400;700&display=swap">
<style>
  :root {
    --page: #e6e7ea;
    --card-dark: #1a1a1a;
    --navy: #1e2f66;
    --navy-soft: #243a7c;
    --white: #ffffff;
    --text-light: #f2f2f2;
  }
  * { box-sizing: border-box; margin: 0; padding: 0; }
  html, body {
    width: 1200px; height: 900px; overflow: hidden;
    background: var(--page);
    font-family: "Open Sans", Arial, sans-serif;
  }
  .sheet {
    width: 1200px; height: 900px;
    display: flex; flex-direction: column; align-items: center; justify-content: center;
    gap: 48px;
  }
  .card {
    width: 620px; height: 354px;
    border-radius: 6px;
    box-shadow: 0 12px 30px rgba(0,0,0,.25);
    position: relative; overflow: hidden;
  }
  /* Front */
  .card--front { background: var(--card-dark); }
  .front-brand {
    position: absolute; left: 150px; top: 34px;
    color: var(--navy-soft);
    font-weight: 400; font-size: 17px; line-height: 1.25;
    width: 260px; text-align: center;
  }
  .front-brand .brand-sub { font-size: 11px; }
  .holder {
    position: absolute; left: 40px; top: 118px;
    padding-left: 16px; border-left: 8px solid var(--navy-soft);
  }
  .holder__name {
    color: var(--navy-soft); font-weight: 700; font-size: 25px; line-height: 1.1;
  }
  .holder__title { color: var(--text-light); font-size: 15px; margin-top: 4px; }
  .contact {
    position: absolute; left: 40px; top: 200px;
    list-style: none; color: var(--text-light); font-size: 15px; line-height: 1.45;
  }
  .contact li { display: flex; align-items: center; gap: 8px; }
  .contact svg { width: 13px; height: 13px; fill: var(--navy-soft); flex: none; }
  .contact .no-icon { padding-left: 21px; }
  .front-decoration {
    position: absolute; right: -30px; top: 70px;
    width: 330px; height: 330px; border-radius: 50%;
    background: radial-gradient(circle at 45% 45%, rgba(36,58,124,.35), rgba(36,58,124,0) 70%);
  }
  /* Back */
  .card--back {
    background: var(--navy);
    display: flex; align-items: center; justify-content: center;
  }
  .back-brand {
    display: flex; align-items: center; gap: 22px; color: var(--white);
    font-weight: 400;
  }
  .back-brand__dot {
    width: 70px; height: 70px; border-radius: 50%; border: 3px solid var(--white); flex: none;
  }
  .back-brand__text { font-size: 34px; line-height: 1.15; }
  .back-brand__text span { display: block; font-size: 19px; margin-top: 6px; }
</style>
</head>
<body>
<main class="sheet">
  <section class="card card--front" aria-label="Card front">
    <div class="front-brand">Harrowgate Dunmere<br><span class="brand-sub">Oral &amp; Maxillofacial Surgery</span></div>
    <div class="holder">
      <p class="holder__name">Dr Elsabet Quorvane,</p>
      <p class="holder__title">DDS board certified</p>
    </div>
    <ul class="contact">
      <li><svg viewBox="0 0 24 24"><path d="M6.6 10.8a15 15 0 0 0 6.6 6.6l2.2-2.2a1 1 0 0 1 1-.25 11 11 0 0 0 3.6.6 1 1 0 0 1 1 1V20a1 1 0 0 1-1 1A17 17 0 0 1 3 4a1 1 0 0 1 1-1h3.5a1 1 0 0 1 1 1c0 1.25.2 2.45.6 3.6a1 1 0 0 1-.25 1z"/></svg>123 456 789</li>
      <li><svg viewBox="0 0 24 24"><path d="M2 5h20v14H2z M2 5l10 8 10-8" /></svg>info@yourgmail.com</li>
      <li><svg viewBox="0 0 24 24"><circle cx="12" cy="12" r="10"/></svg>www.yourwebsite.com</li>
      <li class="no-icon">Your address, City</li>
      <li class="no-icon">State, Zip 1234</li>
    </ul>
    <div class="front-decoration" role="img" aria-label="Large faint brand decoration in navy outline"></div>
  </section>

  <section class="card card--back" aria-label="Card back">
    <div class="back-brand">
      <span class="back-brand__dot"></span>
      <p class="back-brand__text">Harrowgate Dunmere<span>Oral &amp; Maxillofacial Surgery</span></p>
    </div>
  </section>
</main>
</body>
</html>
```